Keystone Trench Co Business Card*

Looking for a professional, clean and crisp business card

I am in the underground utilities industry and am just looking for a really impressive business card. I would like our card to be white with our symbol crisp and clear with it protruding. I also have a business partner that will require his name and info on the card once the design is set. I would like to have our website info on the card which is;
http://keystonetrenchco.example/

Contact Information for Business Card

Website, contact name, number and email

```html
<!DOCTYPE html>
<html lang="en">
<head>
<meta charset="utf-8">
<title>Keystone Trench Co Business Card</title>
<link rel="stylesheet" href="https://fonts.googleapis.com/css2?family=Montserrat:wght@400;600;700&display=swap">
<style>
  :root {
    --canvas: #e6e7e9;
    --card-back: #a6a6a6;
    --card-front: #ffffff;
    --ink: #1d1d1f;
    --muted: #6b6b6b;
    --accent: #3b5bb5;
    --edge: #b9d6ea;
  }
  * { box-sizing: border-box; margin: 0; padding: 0; }
  html, body { width: 1200px; height: 913px; overflow: hidden; }
  body {
    background: var(--canvas);
    font-family: "Montserrat", sans-serif;
    color: var(--ink);
    position: relative;
  }
  .card {
    position: absolute;
    width: 540px;
    height: 309px;
    border-radius: 16px;
    box-shadow: 0 6px 0 var(--edge), 0 14px 26px rgba(0,0,0,.18);
  }
  .card-back {
    left: 50px; top: 60px;
    background: var(--card-back);
    display: flex; align-items: center; justify-content: center;
  }
  .card-front {
    left: 610px; top: 544px;
    background: var(--card-front);
  }
  .brand {
    display: flex; align-items: center; gap: 14px;
    font-weight: 700; font-size: 28px; line-height: 1; color: var(--ink);
    letter-spacing: .01em; white-space: nowrap;
  }
  .brand-dot {
    width: 46px; height: 46px; border-radius: 50%;
    background: var(--ink); flex: none;
  }
  .card-front .brand {
    position: absolute; left: 36px; top: 106px;
  }
  .holder {
    position: absolute; right: 34px; top: 30px; text-align: right;
  }
  .holder-name {
    font-weight: 700; font-size: 21px; letter-spacing: .06em;
  }
  .holder-role {
    font-weight: 400; font-size: 11px; letter-spacing: .1em;
    color: var(--muted); margin-top: 2px;
  }
  .contact {
    position: absolute; left: 140px; bottom: 28px;
    list-style: none; font-size: 14px; line-height: 1.65;
  }
  .contact li { display: flex; align-items: center; gap: 10px; }
  .contact svg { width: 14px; height: 14px; fill: var(--accent); flex: none; }
</style>
</head>
<body>
  <section class="card card-back" aria-label="Card back">
    <div class="brand"><span class="brand-dot"></span>Keystone Trench Co</div>
  </section>

  <section class="card card-front" aria-label="Card front">
    <div class="holder">
      <p class="holder-name">DALE MORROW</p>
      <p class="holder-role">OWNER</p>
    </div>

    <div class="brand"><span class="brand-dot"></span>Keystone Trench Co</div>

    <ul class="contact">
      <li>
        <svg viewBox="0 0 24 24" aria-hidden="true"><path d="M6.6 10.8a15 15 0 0 0 6.6 6.6l2.2-2.2c.3-.3.7-.4 1-.2 1.1.4 2.3.6 3.6.6.6 0 1 .4 1 1V20c0 .6-.4 1-1 1A17 17 0 0 1 3 4c0-.6.4-1 1-1h3.5c.6 0 1 .4 1 1 0 1.3.2 2.5.6 3.6.1.3 0 .7-.2 1z"/></svg>
        604-555-0182(DIG)
      </li>
      <li>
        <svg viewBox="0 0 24 24" aria-hidden="true"><path d="M2 5h20v14H2z M2 5l10 8 10-8" fill="none" stroke="#3b5bb5" stroke-width="2"/></svg>
        dale@keystonetrenchco.example
      </li>
      <li>
        <svg viewBox="0 0 24 24" aria-hidden="true"><circle cx="12" cy="12" r="10"/></svg>
        www.keystonetrenchco.example
      </li>
    </ul>
  </section>
</body>
</html>
```